Business Card Re-Design/Update

We'd like to update out business cards. I've included our current "Style guide" which has the colour scheme of the organisation in it. I've also included the branding files with logos etc in them.

I've also included a copy of one of our existing cards so that you can see how ugly/dated they look. I'd like a fresh modern corporate look.

Target Market(s)

These are for our clients, potential clients, industry contacts - like all business cards

Contact Information for Business Card

Name
Position
Company Address - Level 1, 47 Fernby Street, Carlow Qld 4072
Direct Phone
mobile
Email
Website -www.korvalit.com.au
Logo

Colors

Designer to choose colors to be used in the design.

Requirements
Must have
• Main Logo
• Cards will need to be editable to be able to personalize them for each new employee.
Nice to have
• The MapOut, ShipWell, KeepSteady would be okay to have if they can be sensibly and professionally added to the look without detracting from the main imagery.
• Maybe they could go on the back of the card? will leave this to your creative discretion as to whether/where they fit.
Should not have
• Should not have decorative or script fonts

```html
<!DOCTYPE html>
<html lang="en">
<head>
<meta charset="utf-8">
<title>Korvalit Business Card</title>
<link rel="stylesheet" href="https://fonts.googleapis.com/css2?family=Catamaran:wght@400;500;700&display=swap">
<style>
  :root {
    --stage: #9c9c9c;
    --card-white: #e6e7e7;
    --ink: #231f20;
    --ink-soft: #58595b;
    --brand-red: #d71f26;
    --brand-red-dark: #a8191f;
    --rule: #3a3a3a;
    --on-red: #ffffff;
  }
  html, body {
    margin: 0;
    width: 1200px;
    height: 1200px;
    overflow: hidden;
    background: var(--stage);
    font-family: "Catamaran", Arial, sans-serif;
  }
  .canvas { position: relative; width: 1200px; height: 1200px; }

  .card {
    position: absolute;
    left: 197px;
    width: 809px;
    height: 462px;
    border-radius: 24px;
    overflow: hidden;
  }
  .card-front { top: 94px; background: var(--card-white); }
  .card-back {
    top: 654px;
    background: linear-gradient(100deg, var(--brand-red-dark) 0%, #c81d24 45%, var(--brand-red) 100%);
  }

  .brand {
    position: absolute;
    right: 48px;
    top: 62px;
    display: flex;
    align-items: center;
    gap: 18px;
  }
  .brand-mark {
    width: 58px;
    height: 58px;
    background: var(--brand-red);
  }
  .brand-name {
    font-size: 64px;
    font-weight: 700;
    line-height: 1;
    color: var(--ink);
    letter-spacing: -1px;
  }

  .holder-name {
    position: absolute;
    left: 48px;
    top: 224px;
    margin: 0;
    font-size: 29px;
    font-weight: 700;
    color: var(--brand-red);
    line-height: 1.2;
  }
  .holder-title {
    position: absolute;
    left: 48px;
    top: 262px;
    margin: 0;
    font-size: 18px;
    color: var(--ink-soft);
  }
  .divider {
    position: absolute;
    left: 48px;
    right: 48px;
    top: 302px;
    height: 2px;
    background: var(--rule);
  }

  .contact-list {
    position: absolute;
    left: 48px;
    top: 318px;
    margin: 0;
    padding: 0;
    list-style: none;
    font-size: 17px;
    color: var(--ink-soft);
  }
  .contact-list li {
    display: flex;
    align-items: center;
    gap: 10px;
    height: 29px;
  }
  .contact-icon { width: 15px; height: 15px; fill: var(--brand-red); }

  .address {
    position: absolute;
    right: 48px;
    top: 347px;
    margin: 0;
    font-style: normal;
    text-align: right;
    font-size: 17px;
    line-height: 29px;
    color: var(--ink-soft);
  }

  .footer-band {
    position: absolute;
    left: 0;
    bottom: 0;
    width: 809px;
    height: 50px;
  }
  .website {
    position: absolute;
    right: 48px;
    bottom: 9px;
    font-size: 17px;
    letter-spacing: 1.5px;
    color: var(--on-red);
  }

  .service-line {
    position: absolute;
    left: 0;
    right: 0;
    top: 211px;
    margin: 0;
    text-align: center;
    font-size: 27px;
    font-weight: 500;
    color: var(--on-red);
    word-spacing: 2px;
  }
  .service-line span + span { margin-left: 16px; }
</style>
</head>
<body>
<div class="canvas">

  <section class="card card-front">
    <div class="brand">
      <span class="brand-mark"></span>
      <span class="brand-name">korvalit</span>
    </div>

    <h1 class="holder-name">Maren Holt</h1>
    <p class="holder-title">Business Development Manager</p>
    <div class="divider"></div>

    <ul class="contact-list">
      <li>
        <svg class="contact-icon" viewBox="0 0 24 24"><path d="M6.6 10.8a15.1 15.1 0 0 0 6.6 6.6l2.2-2.2c.3-.3.7-.4 1-.2 1.1.4 2.3.6 3.6.6.6 0 1 .4 1 1V20c0 .6-.4 1-1 1A17 17 0 0 1 3 4c0-.6.4-1 1-1h3.5c.6 0 1 .4 1 1 0 1.3.2 2.5.6 3.6.1.3 0 .7-.2 1z"/></svg>
        +61 (0)7 4188 2060
      </li>
      <li>
        <svg class="contact-icon" viewBox="0 0 24 24"><path d="M6 2h12v6H6z"/><path d="M4 9h16a2 2 0 0 1 2 2v7h-4v4H6v-4H2v-7a2 2 0 0 1 2-2zm4 7v4h8v-4z"/></svg>
        +61 (0)7 4188 2061
      </li>
      <li>
        <svg class="contact-icon" viewBox="0 0 24 24"><path d="M2 5h20v2l-10 6L2 7z"/><path d="M2 9l10 6 10-6v10H2z"/></svg>
        info@korvalit.com.au
      </li>
    </ul>

    <address class="address">
      Level 1, 47 Fernby Street<br>
      Carlow Qld 4072
    </address>

    <svg class="footer-band" viewBox="0 0 809 50" preserveAspectRatio="none">
      <defs>
        <linearGradient id="bandRed" x1="0" x2="1" y1="0" y2="0">
          <stop offset="0" stop-color="#d71f26"/>
          <stop offset="1" stop-color="#a8191f"/>
        </linearGradient>
      </defs>
      <path d="M0 22 L470 22 C500 22 520 14 560 10 L560 12 C522 16 502 28 470 28 L0 28 Z" fill="#231f20"/>
      <path d="M0 36 L470 36 C510 36 530 12 580 12 L809 12 L809 50 L0 50 Z" fill="url(#bandRed)"/>
    </svg>
    <span class="website">www.korvalit.com.au</span>
  </section>

  <section class="card card-back">
    <p class="service-line">
      <span>• The MapOut</span>
      <span>• ShipWell</span>
      <span>• KeepSteady</span>
    </p>
  </section>

</div>
</body>
</html>
```